Bluefern Business Services needs a new interactive and interesting website

We need an interesting, professional, modern and functional company website for Bluefern Business Services - a young IT Services company based out of Chennai, India.

Bluefern Business Services is a fully owned subsidiary of Marlow Goods, one of the world's leading direct to consumer wine merchant.

We already have a registered company logo which must feature in the website.

We conceive, design, develop, test, implement and support IT solutions across the entire Marlow Goods IT landscape. For ex : We currently run about 25 e-commerce websites for Marlow Goods on ATG and Dot Net.

We would like to see our corporate colors used in the website. (Burgundy wine and wine green - source: www.bluefernbs-site.com)

We are looking at this website to communicate a fun, friendly and professionally managed company - reaching out to career seekers, prospective customers and general public.

For reference - The company name 'Bluefern' is an inspiration from the Marlow Goods lineage.

The second image with the world map is stickered on our main entrance to the office, I am not sure where this can be used -just putting it out there..

Please note that there are only a few more days to submit designs for this contest  !

I would appreciate if you can help posting your designs in time for our review and consideration.

Thanks.

Reason: Thanks for your inputs. We have a number of designers and a lot to digest and work with in the past few days. There has been a rush of new designs in the last few days Hence we will require more time to process these and make our decision. Hence i am requesting the contest to be open for more days. Regards, Tarun

Target Market(s)

Prospective job seekers who want to know more about the company and also wish to apply for a job vacancy
People wanting to know more about the company in general and our progress
People who want to see what we offer and how we can help them too - prospective customers
Companies that are interested in our IT Captive journey and are looking for a business opportunity

Industry/Entity Type

E-Commerce

Requirements
Must have
• Log In/ Register facility acting as a Single Sign on for Intranet (Employees)

Facility to post job vacancies (with an expiry date) and enable people to apply for a role and upload their CV/Resume.

Facility to Review Job applications

Facility for website visitors to contact Bluefern business Services via an online 'Contact Us' form with a split of job seekers and business opportunities

Gallery facility to upload pictures regarding company events
Nice to have
• Less Cluttered and contemporary design
Some Wine/Vineyard inspirations will be good but not too much, the company is an IT services company

```html
<!DOCTYPE html>
<html lang="en">
<head>
<meta charset="utf-8">
<title>Bluefern Business Services</title>
<link href="https://fonts.googleapis.com/css2?family=PT+Sans:wght@400;700&family=Arimo:wght@400;700&display=swap" rel="stylesheet">
<style>
:root{
  --burgundy:#7b0b3d;
  --burgundy-dark:#5e072e;
  --olive:#6e7d2b;
  --green:#8aab32;
  --green-light:#a2c443;
  --green-dark:#6f8a25;
  --heading:#454545;
  --body:#4a4a4a;
  --accent:#8c0f40;
  --name-green:#7aa32a;
  --rule:#dcdcdc;
  --clients-bg:#e4e4e4;
  --footer:#222222;
}
*{box-sizing:border-box;margin:0;padding:0}
html,body{width:974px;height:1200px;overflow:hidden;background:#fff}
body{position:relative;font-family:"Arimo",Arial,sans-serif;color:var(--body)}
.abs{position:absolute}
.top-strip{left:0;top:0;width:974px;height:8px;background:var(--olive)}
.header{left:0;top:8px;width:974px;height:448px;background:var(--burgundy)}
.header-line{left:0;top:120px;width:974px;height:3px;background:var(--burgundy-dark)}
.brand{left:118px;top:24px;width:190px;font-family:"PT Sans",sans-serif;font-weight:700;color:#fff;font-size:21px;line-height:22px}
.notice{left:488px;top:30px;width:374px;height:44px;background:var(--burgundy-dark);border-radius:3px;color:#fff;font-family:"PT Sans",sans-serif;font-size:8.9px;line-height:18px;padding:4px 8px;white-space:nowrap;letter-spacing:-.1px}
.notice::after{content:"";position:absolute;left:22px;bottom:-8px;border:8px solid transparent;border-bottom:0;border-top-color:var(--burgundy-dark)}
.nav{left:116px;top:103px;width:746px;height:35px;background:linear-gradient(var(--green-light),var(--green));border:1px solid var(--green-dark);display:flex;font-family:"PT Sans",sans-serif;font-weight:700;font-size:10.5px;color:#fff}
.nav a{display:flex;align-items:center;justify-content:center;color:#fff;text-decoration:none;border-right:1px solid var(--green-dark);height:100%}
.nav a.active{background:linear-gradient(#6f7f2b,#5c6b22)}
.search{margin-left:5px;margin-top:5px;width:183px;height:24px;background:linear-gradient(#fff,#f0f3e6);border:1px solid #c6d69a}
.search-btn{margin-top:5px;width:28px;height:24px;background:linear-gradient(var(--green-light),var(--green-dark));border:1px solid var(--green-dark);display:flex;align-items:center;justify-content:center}
.slider{left:114px;top:151px;width:747px;height:305px;background:#fff;border:1px solid #ddd}
.slide{left:9px;top:9px;width:729px;height:289px;background:linear-gradient(90deg,#c7b8a8,#e7dfd5 35%,#d4d9de 60%,#eceae6)}
.slide-arrow{top:132px;width:18px;height:26px;background:rgba(255,255,255,.55);display:flex;align-items:center;justify-content:center;border-radius:2px}
.dots{left:325px;top:277px;width:96px;height:20px;background:#fff;border-radius:8px 8px 0 0;display:flex;gap:5px;align-items:center;justify-content:center}
.dots i{width:9px;height:9px;border-radius:50%;background:#9a9a9a;display:block}
.dots i.on{background:var(--burgundy)}
.slider-shadow{left:130px;top:456px;width:715px;height:24px;background:radial-gradient(ellipse at top,rgba(0,0,0,.18),transparent 70%)}
.h2{font-family:"PT Sans",sans-serif;font-weight:400;font-size:17.5px;color:var(--heading);text-transform:uppercase;white-space:nowrap;letter-spacing:-.1px}
.rule{height:1px;background:var(--rule)}
.pager{display:flex;gap:2px}
.pager span{width:17px;height:16px;background:#1d1d1d;color:#e0701c;font-size:8px;display:flex;align-items:center;justify-content:center}
.photo{background:linear-gradient(135deg,#d6dcd6,#a7b0ad 50%,#505356)}
.copy{font-size:9.5px;line-height:12.2px;text-align:justify;color:#4d4d4d;hyphens:auto;-webkit-hyphens:auto}
.sub{color:var(--accent);font-size:9.6px}
.svc-list{list-style:none;font-size:9.3px;color:#333}
.svc-list li{height:28px;display:flex;align-items:center;gap:8px}
.svc-list li::before{content:"";width:8px;height:8px;border-radius:50%;background:#222}
.vsep{width:4px;background:#dedede}
.opp{display:flex;gap:8px;height:68px}
.date{width:54px;height:54px;border-radius:50%;background:#5c5b5b;color:#fff;font-family:"PT Sans",sans-serif;font-size:15px;line-height:19px;text-align:center;padding-top:8px;flex:none}
.opp h4{font-weight:400;font-size:9px;color:#222;margin-top:9px;white-space:nowrap}
.opp p{font-size:7px;color:#555;margin-top:6px;white-space:nowrap}
.opp a{font-size:7.5px;color:var(--accent);font-weight:700;text-decoration:none;display:block;margin-top:5px}
.video{left:633px;top:818px;width:228px;height:196px;border:1px solid #ccc}
.video-frame{width:100%;height:182px;background:linear-gradient(120deg,#bcc3c8,#e7e9ea 45%,#6d6f72)}
.controls{height:13px;background:#eee;border-top:1px solid #bbb;display:flex;align-items:center;gap:4px;padding:0 4px;font-size:6px;font-weight:700;color:#222}
.track{flex:1;height:3px;background:#888}
.clients{left:0;top:1042px;width:974px;height:90px;background:var(--clients-bg);border-bottom:3px solid #999}
.client{font-family:"PT Sans",sans-serif;font-weight:700;color:#6a1a35;font-size:14px;top:38px;white-space:nowrap}
.footer{left:0;top:1154px;width:974px;height:46px;background:var(--footer)}
.social{top:15px;width:22px;height:22px;border-radius:50%;background:#333}
</style>
</head>
<body>
<div class="abs top-strip"></div>
<div class="abs header"></div>
<div class="abs header-line"></div>

<div class="abs brand">Bluefern<br>Business Services</div>
<div class="abs notice">Current Opportunities : There are often a number of opportunties available at Bluefern.<br>Here are the latest ones. Be sure to get your application form in before the closing date!</div>

<nav class="abs nav">
  <a class="active" href="#" style="width:94px">HOME</a>
  <a href="#" style="width:138px">ABOUT BLUEFERN</a>
  <a href="#" style="width:100px">SERVICES</a>
  <a href="#" style="width:98px">CAREERS</a>
  <a href="#" style="width:94px;border-right:0">CONTACT</a>
  <div class="search"></div>
  <div class="search-btn"><svg width="12" height="12" viewBox="0 0 12 12"><circle cx="7.5" cy="4.5" r="3" fill="none" stroke="#fff" stroke-width="1.6"/><line x1="5.3" y1="6.7" x2="1.5" y2="10.5" stroke="#fff" stroke-width="2"/></svg></div>
</nav>

<div class="abs slider">
  <div class="abs slide" role="img" aria-label="Photo of a smiling team of business colleagues seated at a meeting table"></div>
  <div class="abs slide-arrow" style="left:12px"><svg width="8" height="12"><polyline points="6,1 2,6 6,11" fill="none" stroke="#fff" stroke-width="2"/></svg></div>
  <div class="abs slide-arrow" style="left:717px;background:rgba(120,120,120,.6)"><svg width="8" height="12"><polyline points="2,1 6,6 2,11" fill="none" stroke="#fff" stroke-width="2"/></svg></div>
  <div class="abs dots"><i></i><i></i><i class="on"></i><i></i><i></i><i></i></div>
</div>
<div class="abs slider-shadow"></div>

<h2 class="abs h2" style="left:117px;top:487px;font-size:19px">Welcome!</h2>
<div class="abs rule" style="left:116px;top:523px;width:478px"></div>
<div class="abs photo" style="left:116px;top:542px;width:197px;height:168px" role="img" aria-label="Photo of two businesswomen working at a laptop"></div>
<div class="abs sub" style="left:320px;top:540px">Delivering IT Excellence</div>
<div class="abs copy" style="left:320px;top:564px;width:274px">
  <p>Welcome to Bluefern Business Services, an emerging provider of global IT consulting and software services. We are part of the Marlow Goods group, a family run business and the world's largest multi-channel home delivery wine merchant...</p>
  <p style="margin-top:12px">Nemo enim ipsam voluptatem quia voluptas sit aspernatur aut odit aut fugit,</p>
  <p style="margin-top:24px">Services, an emerging provider of global IT consulting and software services. We are part of the Marlow Goods group, a family run business and the world's largest multi-channel home deliv-</p>
</div>

<h2 class="abs h2" style="left:634px;top:489px">Testimonials</h2>
<div class="abs pager" style="left:824px;top:491px"><span>&lt;</span><span>&gt;</span></div>
<div class="abs rule" style="left:632px;top:523px;width:228px"></div>
<div class="abs photo" style="left:634px;top:544px;width:76px;height:66px;background:linear-gradient(135deg,#e9e4df,#bfae9c)" role="img" aria-label="Portrait photo of the client giving the testimonial"></div>
<div class="abs copy" style="left:716px;top:546px;width:142px;line-height:13px">Marlow Goods IT landscape. Current plans to strategically transform this landscape to a single set of global systems are underway, across all locations and all</div>
<div class="abs copy" style="left:632px;top:621px;width:228px;line-height:13px">Marlow Goods IT landscape. Current plans to strategically transform this landscape to a single set of global systems are underway, across all locations and all four continents.</div>
<div class="abs copy" style="left:632px;top:686px">Thanks</div>
<div class="abs copy" style="left:632px;top:699px;color:var(--name-green)">Daniel</div>

<div class="abs" style="left:116px;top:736px;width:744px;height:4px;background:#d6d6d6;border-radius:2px"></div>

<h2 class="abs h2" style="left:115px;top:762px">Services</h2>
<div class="abs pager" style="left:307px;top:766px"><span>&lt;</span><span>&gt;</span></div>
<div class="abs rule" style="left:115px;top:798px;width:229px"></div>
<p class="abs copy" style="left:115px;top:813px;width:229px;font-size:9.4px;line-height:14px;color:#333">The services we provide enable the businesses we support to efficiently manage key functions, including order management.</p>
<ul class="abs svc-list" style="left:118px;top:858px">
  <li>Packaged Applications</li>
  <li>Enterprise Application Integration</li>
  <li>Digital Commerce</li>
  <li>Application Development &amp; Maintenance</li>
  <li>Multiple versions of Corelane Commerce</li>
  <li>Ledgerly Suite 2009</li>
</ul>
<div class="abs vsep" style="left:356px;top:760px;height:258px"></div>

<h2 class="abs h2" style="left:371px;top:762px">Latest Opportunities</h2>
<div class="abs pager" style="left:565px;top:766px"><span>&lt;</span><span>&gt;</span></div>
<div class="abs rule" style="left:371px;top:798px;width:227px"></div>
<div class="abs" style="left:366px;top:807px;width:250px">
  <div class="opp"><div class="date">Jan<br>07</div><div><h4>Software Developers/Programmer Analysts</h4><p>LS We are looking for a LS Software Developer join...</p><a href="#">read more &gt;&gt;</a></div></div>
  <div class="opp"><div class="date">Jan<br>07</div><div><h4>Software Developers/Programmer Analysts</h4><p>LS We are looking for a LS Software Developer join...</p><a href="#">read more &gt;&gt;</a></div></div>
  <div class="opp"><div class="date">Jan<br>07</div><div><h4>Software Developers/Programmer Analysts</h4><p>LS We are looking for a LS Software Developer join...</p><a href="#">read more &gt;&gt;</a></div></div>
</div>
<svg class="abs" style="left:426px;top:1005px" width="30" height="14"><circle cx="7" cy="7" r="6" fill="#ccc"/><polygon points="9,4 5,7 9,10" fill="#8c0f40"/><circle cx="23" cy="7" r="6" fill="#ccc"/><polygon points="21,4 25,7 21,10" fill="#8c0f40"/></svg>
<div class="abs vsep" style="left:614px;top:760px;height:258px"></div>

<h2 class="abs h2" style="left:632px;top:762px">Recent Events</h2>
<div class="abs pager" style="left:824px;top:766px"><span>&lt;</span><span>&gt;</span></div>
<div class="abs rule" style="left:632px;top:798px;width:228px"></div>
<div class="abs video">
  <div class="video-frame" role="img" aria-label="Video still of a presenter leading a meeting with colleagues at laptops"></div>
  <svg class="abs" style="left:98px;top:75px" width="40" height="40"><circle cx="20" cy="20" r="19" fill="rgba(40,40,40,.75)"/><polygon points="15,11 29,20 15,29" fill="#fff"/></svg>
  <div class="controls"><svg width="6" height="6"><polygon points="0,0 6,3 0,6" fill="#222"/></svg><span>00:01</span><div class="track"></div><span>100 %</span><span>▪ ◂▮▮</span></div>
</div>

<div class="abs clients">
  <svg class="abs" style="left:116px;top:28px" width="24" height="24"><rect x="0" y="4" width="6" height="20" fill="#9bc43a"/><rect x="7" y="0" width="6" height="24" fill="#c6d04a"/><rect x="14" y="8" width="5" height="16" fill="#3c8fd0"/><rect x="19" y="12" width="5" height="12" fill="#e27a2a"/></svg>
  <div class="abs" style="left:158px;top:40px;font-family:'PT Sans',sans-serif;font-size:11px;color:#333">OUR CLIENTS</div>
  <div class="abs" style="left:243px;top:26px;width:1px;height:42px;background:#ccc"></div>
  <div class="abs client" style="left:272px">Southbank Cellars</div>
  <div class="abs client" style="left:410px">Vinolia House</div>
  <div class="abs client" style="left:542px">Cask Folk</div>
  <div class="abs client" style="left:650px">Marlow Goods</div>
  <div class="abs client" style="left:772px">Harbor Vines</div>
</div>

<div class="abs footer">
  <div class="abs" style="left:117px;top:18px;font-size:9px;color:var(--name-green)">© 2014 bluefernbs.. All Rights Reserved.</div>
  <div class="abs social" style="left:752px"></div>
  <div class="abs social" style="left:778px"></div>
  <div class="abs social" style="left:808px"></div>
  <div class="abs social" style="left:836px"></div>
</div>
</body>
</html>
```